Fernhollow Climate Business Card Design

Design new, 2 sides, business cards for a residential and light commercial heating, air conditioning contractor.

Target Market(s)

Homeowners, small businesses

Industry/Entity Type

Business

Contact Information for Business Card

Dominic Westerhall
Phone - 862-415-2736
Email
Address - PO box 518
Brightwater NJ 07912
Website - www.FernhollowClimateLLC.example

Requirements
Must have
• logo, company colors, standard size with no die cut, so I can use nova stamp

```html
<!DOCTYPE html>
<html lang="en">
<head>
<meta charset="utf-8">
<title>Fernhollow Climate Business Card</title>
<link rel="stylesheet" href="https://fonts.googleapis.com/css2?family=Roboto:wght@400;500;700&display=swap">
<style>
  :root {
    --backdrop: #4a4a4a;
    --card-dark: #252122;
    --card-light: #ffffff;
    --brand-red: #9b1c2e;
    --brand-orange: #f08a24;
    --brand-cream: #f7e6ae;
    --text-grey: #555555;
    --rule-grey: #d6d6d6;
  }
  * { margin: 0; padding: 0; box-sizing: border-box; }
  html, body {
    width: 1200px; height: 1000px; overflow: hidden;
    background: var(--backdrop);
    font-family: "Roboto", Arial, sans-serif;
  }
  .canvas { position: relative; width: 1200px; height: 1000px; }
  .card {
    position: absolute; left: 287px; width: 626px; height: 358px;
    box-shadow: 0 4px 14px rgba(0,0,0,0.35);
  }
  .card-front {
    top: 140px; background: var(--card-dark);
    display: flex; align-items: center; justify-content: center;
  }
  .card-back { top: 531px; background: var(--card-light); }
  .brand-name {
    font-family: "Roboto", Arial, sans-serif; font-weight: 700;
    letter-spacing: 1px; text-transform: uppercase; text-align: center; line-height: 1.05;
  }
  .card-front .brand-name { color: var(--brand-cream); font-size: 52px; }
  .brand-block {
    position: absolute; left: 42px; top: 96px; width: 236px; height: 166px;
    display: flex; align-items: center; justify-content: center;
  }
  .card-back .brand-name { color: var(--brand-red); font-size: 29px; }
  .divider {
    position: absolute; left: 305px; top: 96px; width: 1px; height: 164px;
    background: var(--rule-grey);
  }
  .contact { position: absolute; left: 333px; top: 100px; color: var(--text-grey); }
  .contact-name { color: var(--brand-red); font-weight: 700; font-size: 19.5px; margin-bottom: 16px; }
  .contact-address { font-size: 14.5px; line-height: 18px; margin-bottom: 18px; }
  .contact-list { list-style: none; font-size: 14.5px; line-height: 22px; }
  .contact-list li { display: flex; align-items: center; gap: 7px; }
  .contact-list svg { width: 11px; height: 11px; fill: var(--brand-orange); flex: none; }
</style>
</head>
<body>
<div class="canvas">
  <section class="card card-front">
    <div class="brand-name">Fernhollow<br>Climate</div>
  </section>

  <section class="card card-back">
    <div class="brand-block"><div class="brand-name">Fernhollow<br>Climate</div></div>
    <div class="divider"></div>
    <div class="contact">
      <p class="contact-name">Dominic Westerhall</p>
      <p class="contact-address">PO box 518<br>Brightwater NJ 07912</p>
      <ul class="contact-list">
        <li>
          <svg viewBox="0 0 12 12" aria-hidden="true"><path d="M2.5 0.8 4.3 3.2 3.3 4.5c.7 1.6 2 2.9 3.6 3.6l1.3-1L11 8.9 9.8 11.2C5 11 1 7 .8 2.2Z"/></svg>
          862-415-2736
        </li>
        <li>
          <svg viewBox="0 0 12 12" aria-hidden="true"><path d="M0 2h12v1L6 6.6 0 3Zm0 2.3 6 3.6 6-3.6V10H0Z"/></svg>
          info@FernhollowClimateLLC.example
        </li>
        <li>
          <svg viewBox="0 0 12 12" aria-hidden="true"><path d="M6 0a6 6 0 1 0 0 12A6 6 0 0 0 6 0Zm0 1.2c.8.8 1.4 2.3 1.5 4.2h-3C4.6 3.5 5.2 2 6 1.2ZM1.3 5.4a4.8 4.8 0 0 1 2.6-3.7c-.4 1-.6 2.3-.7 3.7Zm0 1.2h1.9c.1 1.4.3 2.7.7 3.7a4.8 4.8 0 0 1-2.6-3.7Zm4.7 4.2c-.8-.8-1.4-2.3-1.5-4.2h3c-.1 1.9-.7 3.4-1.5 4.2Zm2.1-.5c.4-1 .6-2.3.7-3.7h1.9a4.8 4.8 0 0 1-2.6 3.7Zm.7-4.9c-.1-1.4-.3-2.7-.7-3.7a4.8 4.8 0 0 1 2.6 3.7Z"/></svg>
          www.FernhollowClimateLLC.example
        </li>
      </ul>
    </div>
  </section>
</div>
</body>
</html>
```